zorvan lumet website design

An IT support and IT Security Company - just use dummy text for now for the design. Examples of sites we like the looks and feel of but need it more professional feel are like: www.kelbrovault.uk.com , www.pravok.co.uk, www.quenthardy.com/professional/, www.vur.com, www.melvish.com,

Best to message me if you have any questions

Target Market(s)

small to medium UK based companies that require IT support services

Industry/Entity Type

It Company

Contact Information for Business Card

use dummy name, telephone and email for now, will provide details later.

Logo Text

zorvan lumet (and then below the logo it should say "your IT, networks and security partner")

Coding

Coded - Design and coding required

Number of Pages Required

5+ page

Colors

Designer to choose colors to be used in the design.

Requirements
Must have
• must be professional, yet simple and clear that this is a serious IT support and IT security company.
Nice to have
• 1)The website homepage must have professional quality pictures of IT support or London city skyline or any picture that projects friendly business partners, professionalism and ready to serve.
• 2) Home page needs to include tabs for following pages 'Services' , 'About Us' , 'Contact Us' 'Home'
• 3) Website built customised using wordpress is ideal and easy for us to manage.
• more room for boxed options from homepage (with pic or image in background)
Should not have
• no checkout trolleys or payment options.

```html
<!DOCTYPE html>
<html lang="en">
<head>
<meta charset="utf-8">
<title>Zorvan Lumet – IT Support &amp; Security</title>
<link href="https://fonts.googleapis.com/css2?family=Oswald:wght@400;500&family=Roboto:wght@400;500;700&display=swap" rel="stylesheet">
<style>
:root{
  --orange:#ff5a12;
  --blue:#1b69ab;
  --navy:#0d1a3a;
  --dark:#272727;
  --ink:#222;
  --muted:#777;
  --light:#f2f2f2;
  --white:#fff;
}
*{box-sizing:border-box;margin:0;padding:0}
html,body{width:1200px;height:3163px;overflow:hidden}
body{font-family:"Roboto",Arial,sans-serif;color:var(--ink);background:var(--white);position:relative;font-size:12px}
.abs{position:absolute}
.head{font-family:"Oswald","Arial Narrow",sans-serif;font-weight:500;text-transform:uppercase}
.btn{display:inline-flex;align-items:center;justify-content:center;border-radius:24px;font-family:"Oswald","Arial Narrow",sans-serif;font-size:13px;font-weight:500;text-transform:uppercase;color:var(--white);background:var(--orange)}

/* top bar */
.topbar{left:0;top:0;width:1200px;height:42px;display:flex;align-items:center;justify-content:flex-end;gap:34px;padding-right:200px;font-size:12px;color:#333}
.topbar span{display:flex;align-items:center;gap:8px}

/* hero */
.hero{left:0;top:42px;width:1200px;height:601px;background:linear-gradient(100deg,#1d2a38 0%,#3a4d62 40%,#6f8498 70%,#a9b8c6 100%)}
.hero-shade{inset:0;background:linear-gradient(180deg,rgba(0,0,0,.15),rgba(0,0,0,.35))}
.nav{left:200px;top:38px;width:802px;height:59px;background:rgba(30,30,30,.78);display:flex;align-items:center}
.logo{width:222px;height:59px;background:var(--white);display:flex;align-items:center;gap:8px;padding-left:14px}
.logo-dot{width:22px;height:22px;border-radius:50%;background:var(--orange)}
.logo-name{font-family:"Oswald",sans-serif;font-weight:500;font-size:20px;color:var(--navy);text-transform:uppercase;line-height:1}
.nav ul{list-style:none;display:flex;align-items:center;margin-left:38px;font-size:13px;color:var(--white);font-weight:500}
.nav li{padding:0 26px;border-left:1px solid rgba(255,255,255,.6);line-height:14px}
.nav li:first-child{border-left:0;color:var(--orange);position:relative}
.nav li:first-child::after{content:"";position:absolute;left:26px;right:26px;bottom:-8px;height:2px;background:var(--orange)}
.nav .search{margin-left:auto;margin-right:22px;display:flex;align-items:center;gap:8px;color:var(--white);font-size:13px;font-weight:500}
.hero h1{left:200px;top:248px;font-size:62px;color:var(--white);letter-spacing:.5px;font-weight:500}
.hero-text{left:200px;top:336px;width:690px;color:var(--white);font-size:13px;line-height:22px;font-weight:500}
.hero .btn{height:46px;width:158px;top:427px}
.btn-ghost{background:transparent;border:2px solid var(--white)}
.slide-arrow{width:46px;height:46px;border-radius:50%;background:rgba(255,255,255,.85);top:307px;display:flex;align-items:center;justify-content:center}

/* intro */
.intro{left:0;top:643px;width:1200px;height:306px;text-align:center}
.intro h2{font-size:34px;margin-top:48px;color:var(--ink)}
.intro p{width:704px;margin:18px auto 0;font-size:12px;line-height:22px;color:#444}
.intro .btn{width:164px;height:46px;margin-top:40px}

/* about */
.about{left:0;top:949px;width:1200px;height:707px;background:linear-gradient(115deg,#f4f5f7 0%,#e9ecef 45%,#dfe3e8 75%,#eef0f2 100%)}
.title-rule{width:46px;height:3px;background:var(--orange);margin:10px auto 0}
.about h2{font-size:32px;text-align:center;margin-top:66px}
.about .lead{width:720px;margin:16px auto 0;text-align:center;font-size:12px;font-weight:500;line-height:20px}
.about-photo{left:200px;top:211px;width:376px;height:416px;background:linear-gradient(135deg,#d9c7c4 0%,#b8a7a5 40%,#6f7782 75%,#4a5260 100%)}
.feature{left:601px;width:420px;display:flex;gap:10px}
.feature-icon{width:50px;height:50px;background:var(--blue);border-radius:4px;flex:none;display:flex;align-items:center;justify-content:center}
.feature h3{font-size:14px;font-weight:500;text-transform:uppercase;font-family:"Roboto",sans-serif;margin-top:14px}
.feature p{font-size:12px;line-height:20px;color:#555;margin-top:16px;margin-left:-60px;width:400px}

/* services band */
.band{left:0;top:1656px;width:1200px;height:130px;background:var(--orange);text-align:center;color:var(--white)}
.band h2{font-size:33px;margin-top:22px}
.band p{font-size:12px;font-weight:500;margin-top:8px}
.band-notch{left:585px;top:1786px;width:0;height:0;border-left:15px solid transparent;border-right:15px solid transparent;border-top:14px solid var(--orange)}

.card{top:1856px;width:241px;height:369px;background:var(--light);border-bottom:5px solid var(--orange);padding:48px 24px 0 24px}
.card.active{background:var(--blue);color:var(--white)}
.card h3{font-family:"Roboto",sans-serif;font-size:13px;font-weight:500;margin-top:20px}
.card .rule{width:46px;height:3px;background:var(--orange);margin-top:16px}
.card p{font-size:11px;line-height:20px;color:#888;margin-top:16px}
.card.active p{color:#e8eef5}
.card .btn{width:108px;height:32px;margin-top:28px;font-size:12px}
.card.active .btn{background:transparent;border:2px solid var(--white)}

.divider{left:0;top:2288px;width:1200px;height:1px;background:#e3e3e3}

/* news */
.news-box{left:200px;top:2345px;width:272px;height:407px;background:var(--navy);color:var(--white)}
.news-box .cap{height:66px;background:#efefef;padding:14px 20px}
.news-box .cap h2{color:var(--blue);font-size:30px;font-weight:500}
.news-box p{font-size:12px;line-height:22px;padding:22px 20px 0 20px;font-weight:500}
.field{left:19px;width:215px;height:41px;background:var(--white);color:#999;font-size:11px;display:flex;align-items:center;padding-left:12px}
.news-box .btn{left:19px;top:333px;width:112px;height:32px;border-radius:16px;font-size:12px}
.news-item{left:498px;width:170px}
.news-item h4{font-size:11px;font-weight:500;line-height:18px;text-transform:uppercase}
.news-item time{font-size:11px;color:#444;display:block;margin-top:2px}
.news-card{left:681px;top:2358px;width:319px;height:390px;background:var(--white);box-shadow:0 2px 12px rgba(0,0,0,.15);padding:4px}
.news-photo{width:311px;height:190px;background:radial-gradient(circle at 55% 55%,#5fb8d6 0%,#1d5d86 40%,#0a2540 80%)}
.news-card h4{font-size:12px;font-weight:500;line-height:19px;margin:14px 18px 0;text-transform:uppercase}
.news-card time{display:block;font-size:11px;margin:8px 18px 0;color:#444}
.news-card p{font-size:11px;line-height:18px;margin:12px 18px 0;color:#555}
.news-card a{display:inline-block;font-size:11px;font-weight:700;color:var(--blue);margin:12px 18px 0;border-bottom:1px solid var(--blue)}
.mini-arrow{width:24px;height:24px;border-radius:50%;background:var(--white);box-shadow:0 1px 4px rgba(0,0,0,.2);top:2567px;display:flex;align-items:center;justify-content:center}

/* footer */
.footer{left:0;top:2822px;width:1200px;height:341px;background:var(--dark);color:var(--white)}
.fcol{top:64px}
.fcol h4{font-size:12px;font-weight:700;text-transform:uppercase;display:flex;align-items:center;gap:10px;height:28px}
.fcol ul{list-style:none;margin-top:12px}
.fcol li{font-size:12px;line-height:24px;display:flex;align-items:flex-start;gap:14px}
.brand h4{font-family:"Oswald",sans-serif;font-size:21px;color:var(--orange);font-weight:500}
.brand p{font-size:12px;line-height:22px;margin-top:12px;width:232px}
.social-dot{width:10px;height:10px;border-radius:50%;background:var(--white);margin-top:7px;flex:none}
.foot-line{left:200px;top:294px;width:800px;height:1px;background:#4a4a4a}
.copyright{left:200px;top:310px;font-size:11px}
.foot-nav{right:200px;top:310px;font-size:11px;display:flex}
.foot-nav span{padding:0 18px;border-left:1px solid #999;line-height:12px}
.foot-nav span:first-child{border-left:0}
.foot-nav span:last-child{padding-right:0}
</style>
</head>
<body>

<div class="abs topbar">
  <span><svg width="14" height="11" viewBox="0 0 14 11"><rect x="0.5" y="0.5" width="13" height="10" fill="none" stroke="#ff5a12"/><path d="M1 1l6 5 6-5" fill="none" stroke="#ff5a12"/></svg>info@zorvanlumet.com</span>
  <span><svg width="14" height="14" viewBox="0 0 24 24"><path d="M6.6 10.8a15 15 0 006.6 6.6l2.2-2.2a1 1 0 011-.25 11 11 0 003.5.56 1 1 0 011 1V20a1 1 0 01-1 1A17 17 0 013 4a1 1 0 011-1h3.5a1 1 0 011 1 11 11 0 00.56 3.5 1 1 0 01-.25 1z" fill="#ff5a12"/></svg>Call Us : +44 20 7946 0321</span>
  <span><svg width="12" height="15" viewBox="0 0 12 15"><path d="M6 0a6 6 0 00-6 6c0 4.5 6 9 6 9s6-4.5 6-9a6 6 0 00-6-6zm0 8.5A2.5 2.5 0 116 3.5a2.5 2.5 0 010 5z" fill="#ff5a12"/></svg>Lorem ipsum is simple dummy text</span>
</div>

<section class="abs hero" role="img" aria-label="Photo of IT engineers working in a server room">
  <div class="abs hero-shade"></div>
  <nav class="abs nav">
    <div class="logo"><span class="logo-dot"></span><span class="logo-name">Zorvan Lumet</span></div>
    <ul><li>Services</li><li>About Us</li><li>Contact Us</li><li>Home</li></ul>
    <div class="search">Search <svg width="15" height="15" viewBox="0 0 15 15"><circle cx="6" cy="6" r="4.8" fill="none" stroke="#ff5a12" stroke-width="2"/><path d="M9.5 9.5l4.5 4.5" stroke="#ff5a12" stroke-width="2"/></svg></div>
  </nav>
  <h1 class="abs head">Welcome to Zorvan Lumet</h1>
  <p class="abs hero-text">Lorem Ipsum is simply dummy text of the printing and typesetting industry. Lorem Ipsum has been the industry's standard dummy text ever since the 1500s, when an unknown printer took a galley of type...</p>
  <span class="abs btn" style="left:200px">Contact Us</span>
  <span class="abs btn btn-ghost" style="left:376px">Read More</span>
  <span class="abs slide-arrow" style="left:78px"><svg width="14" height="14" viewBox="0 0 14 14"><path d="M9 2L4 7l5 5" fill="none" stroke="#333" stroke-width="2.5"/></svg></span>
  <span class="abs slide-arrow" style="left:1076px"><svg width="14" height="14" viewBox="0 0 14 14"><path d="M5 2l5 5-5 5" fill="none" stroke="#333" stroke-width="2.5"/></svg></span>
</section>

<section class="abs intro">
  <h2 class="head">IT Support for your Industry</h2>
  <p>Lorem Ipsum is simply dummy text of the printing and typesetting industry. Lorem Ipsum has been the industry's standard dummy text ever since the 1500s, when an unknown printer took a galley of type and scrambled it to make a type specimen book. It has survived not only five centuries, but also the leap into electronic typesetting, remaining essentially unchanged.</p>
  <span class="btn">Contact Us</span>
</section>

<section class="abs about">
  <h2 class="head">About Us</h2>
  <div class="title-rule"></div>
  <p class="lead">Lorem Ipsum is simply dummy text of the printing and typesetting industry. Lorem Ipsum has been the industry's standard dummy text ever since the 1500s, when an unknown printer took a galley of type and scrambled it to make a type specimen book.</p>
  <div class="abs about-photo" role="img" aria-label="Photo of two colleagues working together at a computer"></div>
  <div class="abs feature" style="top:253px">
    <div class="feature-icon"><svg width="28" height="28" viewBox="0 0 28 28"><circle cx="14" cy="14" r="10" fill="none" stroke="#fff" stroke-width="2"/><text x="14" y="18" font-size="9" font-family="Roboto" font-weight="700" fill="#fff" text-anchor="middle">24</text></svg></div>
    <div><h3>24/7 IT Support</h3><p>Lorem Ipsum is simply dummy text of the printing and typesetting industry. Lorem Ipsum has been the industry's text here...</p></div>
  </div>
  <div class="abs feature" style="top:392px">
    <div class="feature-icon"><svg width="28" height="28" viewBox="0 0 28 28"><circle cx="14" cy="15" r="9" fill="none" stroke="#fff" stroke-width="2"/><path d="M14 15V10M14 15l4 2M11 4h6" stroke="#fff" stroke-width="2"/></svg></div>
    <div><h3>Super Fast Service</h3><p>Lorem Ipsum is simply dummy text of the printing and typesetting industry. Lorem Ipsum has been the industry's text here...</p></div>
  </div>
  <div class="abs feature" style="top:527px">
    <div class="feature-icon"><svg width="28" height="28" viewBox="0 0 28 28"><path d="M14 4a7 7 0 00-4 12.7V20h8v-3.3A7 7 0 0014 4z" fill="none" stroke="#fff" stroke-width="2"/><path d="M11 23h6" stroke="#fff" stroke-width="2"/></svg></div>
    <div><h3>IT Expertise</h3><p>Lorem Ipsum is simply dummy text of the printing and typesetting industry. Lorem Ipsum has been the industry's text here...</p></div>
  </div>
</section>

<section class="abs band">
  <h2 class="head">Our Services</h2>
  <p>Lorem Ipsum is simply dummy text of the printing and typesetting industry. Lorem Ipsum has been the industry's</p>
</section>
<div class="abs band-notch"></div>

<article class="abs card" style="left:200px">
  <svg width="58" height="58" viewBox="0 0 58 58"><rect x="20" y="16" width="18" height="26" fill="#1b69ab"/><path d="M12 22a18 18 0 0128-10M46 36a18 18 0 01-28 10" fill="none" stroke="#1b69ab" stroke-width="3"/><path d="M40 6v7h-7M18 52v-7h7" fill="none" stroke="#1b69ab" stroke-width="3"/></svg>
  <h3>BUSINESS CONTINUITY</h3><div class="rule"></div>
  <p>Lorem Ipsum is simply dummy text of the printing and typesetting industry. Lorem Ipsum has been the industry's standard dummy text</p>
  <span class="btn">Contact Us</span>
</article>
<article class="abs card active" style="left:481px">
  <svg width="58" height="58" viewBox="0 0 58 58"><circle cx="29" cy="16" r="7" fill="none" stroke="#fff" stroke-width="3"/><path d="M8 36l10 14h22l10-14-8-4-8 8H24l-8-8z" fill="none" stroke="#fff" stroke-width="3"/></svg>
  <h3>IT SUPPORT &amp; FIELD SERVICES</h3><div class="rule"></div>
  <p>Lorem Ipsum is simply dummy text of the printing and typesetting industry. Lorem Ipsum has been the industry's standard dummy text</p>
  <span class="btn">Contact Us</span>
</article>
<article class="abs card" style="left:761px">
  <svg width="58" height="58" viewBox="0 0 58 58"><circle cx="29" cy="20" r="12" fill="#1b69ab"/><path d="M8 56c0-13 9-20 21-20s21 7 21 20z" fill="#1b69ab"/><path d="M15 22a14 14 0 0128 0" fill="none" stroke="#1b69ab" stroke-width="3"/></svg>
  <h3>OUTSOURCED SERVICE DESK</h3><div class="rule"></div>
  <p>Lorem Ipsum is simply dummy text of the printing and typesetting industry. Lorem Ipsum has been the industry's standard dummy text</p>
  <span class="btn">Contact Us</span>
</article>

<div class="abs divider"></div>

<section class="abs news-box">
  <div class="cap"><h2 class="head">Our News</h2></div>
  <p>Lorem Ipsum is simply dummy text of the printing and typesetting industry. Lorem Ipsum has been dummy text</p>
  <div class="abs field" style="top:196px">Name</div>
  <div class="abs field" style="top:260px">E-Mail Address</div>
  <span class="abs btn">Subscribe</span>
</section>

<div class="abs news-item" style="top:2360px"><h4>Lorem Ipsum is simply dummy text of the printing</h4><time>8 Feb-2018</time></div>
<div class="abs news-item" style="top:2442px"><h4>Lorem Ipsum is simply dummy text of the printing</h4><time>8 Feb-2018</time></div>
<div class="abs news-item" style="top:2524px"><h4>Lorem Ipsum is simply dummy text of the printing</h4><time>8 Feb-2018</time></div>
<div class="abs news-item" style="top:2604px"><h4>Lorem Ipsum is simply dummy text of the printing</h4><time>8 Feb-2018</time></div>
<div class="abs news-item" style="top:2686px"><h4>Lorem Ipsum is simply dummy text of the printing</h4><time>8 Feb-2018</time></div>

<article class="abs news-card">
  <div class="news-photo" role="img" aria-label="Illustration of a hand touching a glowing digital network interface"></div>
  <h4>Lorem Ipsum is simply dummy text of the textprinting and typesetting..</h4>
  <time>8 Feb-2018</time>
  <p>Lorem Ipsum is simply dummy text of the printing and typesetting industry. Lorem Ipsum has been the industry's standard dummy text here.....</p>
  <a>READ MORE</a>
</article>
<span class="abs mini-arrow" style="left:669px"><svg width="10" height="10" viewBox="0 0 10 10"><path d="M7 1L3 5l4 4" fill="none" stroke="#333" stroke-width="2"/></svg></span>
<span class="abs mini-arrow" style="left:988px"><svg width="10" height="10" viewBox="0 0 10 10"><path d="M3 1l4 4-4 4" fill="none" stroke="#333" stroke-width="2"/></svg></span>

<footer class="abs footer">
  <div class="abs fcol brand" style="left:200px">
    <h4>ZORVAN LUMET</h4>
    <p>Lorem Ipsum is simply dummy text of the printing and typesetting industry. Lorem Ipsum has been the industry's standard dummy text ever since the 1500s, when an unknown printer took a galley of type and scrambled it to make a type specimen book.</p>
  </div>
  <div class="abs fcol" style="left:464px">
    <h4><svg width="18" height="16" viewBox="0 0 18 16"><path d="M1 6l8-5 8 5v9H1z" fill="none" stroke="#fff" stroke-width="1.6"/><path d="M1 6l8 5 8-5" fill="none" stroke="#fff" stroke-width="1.6"/></svg>Contact Us</h4>
    <ul>
      <li><svg width="13" height="13" viewBox="0 0 24 24" style="margin-top:5px"><path d="M6.6 10.8a15 15 0 006.6 6.6l2.2-2.2a1 1 0 011-.25 11 11 0 003.5.56 1 1 0 011 1V20a1 1 0 01-1 1A17 17 0 013 4a1 1 0 011-1h3.5a1 1 0 011 1 11 11 0 00.56 3.5 1 1 0 01-.25 1z" fill="#fff"/></svg>+44 20 7946 0321</li>
      <li><svg width="11" height="14" viewBox="0 0 12 15" style="margin-top:5px"><path d="M6 0a6 6 0 00-6 6c0 4.5 6 9 6 9s6-4.5 6-9a6 6 0 00-6-6zm0 8.5A2.5 2.5 0 116 3.5a2.5 2.5 0 010 5z" fill="#fff"/></svg><span>Lorem Ipsum is simply dummy text<br>of the printing</span></li>
      <li><svg width="14" height="11" viewBox="0 0 14 11" style="margin-top:7px"><rect x="0.5" y="0.5" width="13" height="10" fill="none" stroke="#fff"/><path d="M1 1l6 5 6-5" fill="none" stroke="#fff"/></svg>info@zorvanlumet.uk</li>
      <li><svg width="14" height="14" viewBox="0 0 14 14" style="margin-top:5px"><path d="M6 8l2-2M5 5l2-2a2.5 2.5 0 013.5 3.5l-2 2M9 9l-2 2a2.5 2.5 0 01-3.5-3.5l2-2" fill="none" stroke="#fff" stroke-width="1.5"/></svg>https://www.zorvanlumet.uk</li>
    </ul>
  </div>
  <div class="abs fcol" style="left:728px">
    <h4><svg width="18" height="18" viewBox="0 0 18 18"><rect x="1" y="1" width="16" height="16" fill="none" stroke="#fff" stroke-width="1.6"/><path d="M4 9l4 4 7-9" fill="none" stroke="#fff" stroke-width="2"/></svg>Quick Links</h4>
    <ul><li>Privacy Policy</li><li>Terms and Condition</li><li>Site Map</li><li>Help</li><li>Request a Quote</li></ul>
  </div>
  <div class="abs fcol" style="left:888px">
    <h4><svg width="16" height="16" viewBox="0 0 14 14"><path d="M6 8l2-2M5 5l2-2a2.5 2.5 0 013.5 3.5l-2 2M9 9l-2 2a2.5 2.5 0 01-3.5-3.5l2-2" fill="none" stroke="#fff" stroke-width="1.5"/></svg>Social Links</h4>
    <ul>
      <li><span class="social-dot"></span>Chatterly</li>
      <li><span class="social-dot"></span>Birdline</li>
      <li><span class="social-dot"></span>Pinboardly</li>
      <li><span class="social-dot"></span>Searchwell</li>
    </ul>
  </div>
  <div class="abs foot-line"></div>
  <div class="abs copyright">© Copyright 2018 zorvanlumet.uk. All Rights Reserved.</div>
  <div class="abs foot-nav"><span>Services</span><span>About Us</span><span>Contact Us</span><span>Home</span></div>
</footer>

</body>
</html>
```